Marlow Vale Stud website

We would like to create a horse stud/agistment farm website similar to this websites we have attached below:
www.thornbeck.com.au
www.quillstead.com.au
www.brackley.com
www.pimsey.com.au
The main colour scheme are purple and white to align with the stable's racing colours.
We have also attach the company logo and also images of the farm and create some ideas for the website.
Many thanks for looking into this project!

```html
<!DOCTYPE html>
<html lang="en">
<head>
<meta charset="utf-8">
<title>Marlow Vale Stud</title>
<link href="https://fonts.googleapis.com/css2?family=Roboto+Slab:wght@300;400;700&display=swap" rel="stylesheet">
<style>
:root{
  --purple:#3a1745;
  --purple-band:#3f1d49;
  --purple-deep:#2c1035;
  --white:#ffffff;
  --ink:#333333;
  --muted:#555555;
  --grey-bg:#ececec;
  --grey-year:#b5b5b5;
  --footer:#4a4a4a;
  --btn-grey:#555555;
  --slab:'Roboto Slab', 'Rockwell', 'DejaVu Serif', serif;
  --sans:Arial, Helvetica, sans-serif;
}
*{box-sizing:border-box;margin:0;padding:0}
html,body{width:1200px;height:3327px;overflow:hidden;background:var(--white)}
body{position:relative;font-family:var(--sans);color:var(--ink)}
.abs{position:absolute}

/* header */
.site-header{left:0;top:0;width:1200px;height:111px;background:var(--white)}
.brand{left:111px;top:34px;display:flex;align-items:center;gap:14px}
.brand-dot{width:44px;height:44px;border-radius:50%;background:var(--purple)}
.brand-name{font-family:var(--slab);font-weight:400;font-size:30px;color:var(--purple);white-space:nowrap}
.main-nav{top:46px;left:0;width:1200px;font-family:var(--slab);font-size:15px;color:var(--ink)}
.main-nav span{position:absolute;white-space:nowrap}

/* hero */
.hero{left:0;top:111px;width:1200px;height:628px;
  background:linear-gradient(180deg,#3f6fb8 0%,#8fb2e0 35%,#cfd9e6 55%,#5a4a38 72%,#4f7a2c 88%,#3d6a22 100%)}
.hero-title{left:428px;top:526px;width:344px;height:57px;background:rgba(58,23,69,.92);
  color:var(--white);font-family:var(--slab);font-size:26px;display:flex;align-items:center;justify-content:center}
.hero-sub{left:339px;top:603px;width:524px;height:58px;background:rgba(70,70,70,.75);
  color:var(--white);font-family:var(--slab);font-size:18px;display:flex;align-items:center;justify-content:center;white-space:nowrap}

/* service cards */
.service{top:772px;width:235px;height:262px}
.service-photo{height:200px}
.service-label{height:62px;background:var(--purple);color:var(--white);font-family:var(--slab);
  font-size:15px;line-height:24px;display:flex;align-items:center;justify-content:center;text-align:center}

/* welcome */
.welcome-photo{left:111px;top:1109px;width:508px;height:364px;
  background:linear-gradient(180deg,#3a2e22 0%,#6a5a40 30%,#4f8a35 70%,#c84a6a 85%,#3f7a2a 100%)}
.welcome-kicker{left:661px;top:1122px;font-family:var(--slab);font-weight:300;font-size:25px;color:var(--ink)}
.welcome-title{left:661px;top:1152px;font-family:var(--slab);font-weight:300;font-size:44px;color:var(--purple);white-space:nowrap}
.welcome-text{left:665px;width:405px;font-size:11.5px;line-height:22.5px;color:var(--muted)}

/* testimonials */
.testimonials{left:0;top:1526px;width:1200px;height:357px;
  background:linear-gradient(180deg,#4a2a55 0%,var(--purple-band) 45%,var(--purple-deep) 100%);color:var(--white);text-align:center}
.testimonials h2{position:absolute;top:50px;left:0;width:1200px;font-family:var(--slab);font-weight:300;font-size:40px}
.testimonials p{position:absolute;top:140px;left:285px;width:630px;font-size:11.5px;line-height:28px}
.t-name{position:absolute;top:245px;left:0;width:1200px;font-family:var(--slab);font-size:18px}
.t-date{position:absolute;top:276px;left:0;width:1200px;font-family:var(--slab);font-weight:300;font-size:15px}

/* year slider */
.year-band{left:0;top:1883px;width:1200px;height:508px;background:var(--grey-bg)}
.year-photo{left:231px;top:2029px;width:723px;height:362px;
  background:radial-gradient(ellipse at 50% 50%,#ffffff 0%,#e6e4e0 50%,rgba(236,236,236,0) 100%)}
.year{left:142px;top:1860px;z-index:2;font-family:var(--slab);font-weight:700;font-size:216px;line-height:1;color:var(--grey-year);letter-spacing:-2px}
.arrow{top:2120px;width:32px;height:32px;z-index:2}
.year-text{left:741px;top:2272px;width:400px;z-index:2;font-family:var(--slab);font-weight:300;font-size:12px;line-height:29px;color:#444}

/* blog */
.blog-title{left:0;top:2436px;width:1200px;text-align:center;font-family:var(--slab);font-weight:300;font-size:42px;color:var(--purple)}
.blog-sub{left:0;top:2506px;width:1200px;text-align:center;font-family:var(--slab);font-weight:300;font-size:14px;color:var(--ink)}
.post{top:2562px;width:306px;height:345px}
.post-photo{position:absolute;left:0;top:0;width:306px;height:217px}
.post-date{position:absolute;left:5px;top:6px;width:50px;height:52px;background:rgba(60,60,60,.85);color:var(--white);
  text-align:center;font-family:var(--slab)}
.post-date b{display:block;font-weight:400;font-size:28px;line-height:32px}
.post-date i{display:block;font-style:normal;font-size:13px;line-height:14px}
.post-card{position:absolute;left:18px;top:179px;width:270px;height:142px;background:var(--white);
  box-shadow:0 1px 4px rgba(0,0,0,.25);padding:14px 17px}
.post-card h3{font-family:var(--slab);font-weight:300;font-size:15px;line-height:25px;color:var(--ink)}
.post-card p{margin-top:8px;font-size:10.5px;line-height:18px;color:var(--muted)}
.read-more{position:absolute;left:80px;top:308px;width:148px;height:35px;background:var(--btn-grey);color:var(--white);
  font-family:var(--slab);font-size:15px;display:flex;align-items:center;justify-content:center}
.read-more.is-featured{background:var(--purple)}

/* footer */
.site-footer{left:0;top:2985px;width:1200px;height:342px;background:var(--footer);color:var(--white)}
.footer-brand{position:absolute;top:58px;left:0;width:1200px;display:flex;justify-content:center;align-items:center;gap:12px}
.footer-brand .brand-dot{width:38px;height:38px}
.footer-brand .brand-name{font-size:28px}
.footer-nav{position:absolute;top:184px;left:0;width:1200px;text-align:center;font-family:var(--slab);font-size:14px}
.footer-nav span{margin:0 22px}
.footer-contact{position:absolute;top:241px;left:0;width:1200px;display:flex;justify-content:center;gap:44px;font-size:11.5px}
.footer-contact div{display:flex;align-items:center;gap:10px}
.copyright{position:absolute;top:287px;left:0;width:1200px;text-align:center;font-size:10.5px}
</style>
</head>
<body>

<header class="site-header abs">
  <div class="brand abs"><span class="brand-dot"></span><span class="brand-name">Marlow Vale Stud</span></div>
  <nav class="main-nav abs">
    <span style="left:620px">Home</span>
    <span style="left:709px">About Us</span>
    <span style="left:820px">Services</span>
    <span style="left:926px">News</span>
    <span style="left:1013px">Contact Us</span>
  </nav>
</header>

<section class="hero abs" role="img" aria-label="Photo of five dark bay horses looking down over a green paddock under a blue cloudy sky"></section>
<div class="hero-title abs">Marlow Vale Stud</div>
<div class="hero-sub abs">Sed ut perspiciatis unde omnis iste natus error sit volu</div>

<div class="service abs" style="left:111px">
  <div class="service-photo" role="img" aria-label="Photo of a chestnut stallion standing by a hedge" style="background:linear-gradient(180deg,#6f8a5a,#9a6a40 60%,#b8a888)"></div>
  <div class="service-label">Silver Lantern (USA)</div>
</div>
<div class="service abs" style="left:357px">
  <div class="service-photo" role="img" aria-label="Photo of a chestnut horse grazing beside a feed tub" style="background:linear-gradient(180deg,#9fc7e8,#6a9a3c 45%,#4f8a2a)"></div>
  <div class="service-label">Weanling &amp; Yearling<br>Sales Preparation</div>
</div>
<div class="service abs" style="left:605px">
  <div class="service-photo" role="img" aria-label="Photo of a pale palomino horse in a green paddock" style="background:linear-gradient(180deg,#4f7a3a,#7aa050 50%,#5a8a30)"></div>
  <div class="service-label">Breaking/ Re-education<br>of problem horses</div>
</div>
<div class="service abs" style="left:852px">
  <div class="service-photo" role="img" aria-label="Photo of horses grazing near tall trees at dusk" style="background:linear-gradient(180deg,#b8c4d0,#5a6a50 50%,#3f5a2a)"></div>
  <div class="service-label">Facility hire</div>
</div>

<div class="welcome-photo abs" role="img" aria-label="Photo of a grey racehorse and jockey in purple silks galloping past flower beds"></div>
<div class="welcome-kicker abs">Welcome to</div>
<div class="welcome-title abs">Marlow Vale Stud</div>
<p class="welcome-text abs" style="top:1231px">Sed ut perspiciatis unde omnis iste natus error sit voluptatem accusant ium doloremque laudantium, totam rem aperiam, eaque ipsa quae ab illo inve ntore veritatis et quasi architecto beatae vitae dicta sunt explicabo. Nemo enim ipsam voluptatem quia voluptas sit aspernatur aut odit aut dolores eos qui ratione voluptatem sequi nesciunt.</p>
<p class="welcome-text abs" style="top:1385px">Neque porro quisquam est, qui dolorem ipsum quia dolor sit amet, consecte tur adipisci velit, sed quia non numquam eius modi tempora incidu nt ut lab ore et dolore magnam aliquam quaerat voluptatem.</p>

<section class="testimonials abs" role="img" aria-label="Dusky purple-tinted photo of trees over a paddock behind the testimonial">
  <h2>Our Testimonials</h2>
  <p>Sed ut perspiciatis unde omnis iste natus error sit voluptatem accusantium doloremque laudantium, totam rem aperiam, eaque ipsa quae ab illo inventore veritatis et quasi architecto beatae vitae dicta sunt explicabo. Nemo aut fugit, sed quia consequuntur magni dolores eos qui ratione voluptatem sequi nesciunt.</p>
  <div class="t-name">Jhon Smith</div>
  <div class="t-date">Posed on 07 mar 2019</div>
</section>

<div class="year-band abs"></div>
<div class="year-photo abs" role="img" aria-label="Illustration of three white horses galloping through mist"></div>
<div class="year abs">2019</div>
<svg class="arrow abs" style="left:113px" viewBox="0 0 32 32"><circle cx="16" cy="16" r="15" fill="none" stroke="#555" stroke-width="1.5"/><path d="M18.5 10.5 13 16l5.5 5.5" fill="none" stroke="#555" stroke-width="2"/></svg>
<svg class="arrow abs" style="left:1051px" viewBox="0 0 32 32"><circle cx="16" cy="16" r="15" fill="none" stroke="#555" stroke-width="1.5"/><path d="M13.5 10.5 19 16l-5.5 5.5" fill="none" stroke="#555" stroke-width="2"/></svg>
<p class="year-text abs">Sed ut perspiciatis unde omnis iste natus error sit voluptatem accusantium doloremque laudantium, totam rem aperiam, eaque inventore veritatis et quasi architecto beatae</p>

<h2 class="blog-title abs">Latest Blog</h2>
<p class="blog-sub abs">Sed ut perspiciatis unde omnis iste natus error sit voluptatem accusantium doloremque laudantium</p>

<article class="post abs" style="left:111px">
  <div class="post-photo" role="img" aria-label="Photo of a paddock at sunset with horses under trees" style="background:linear-gradient(180deg,#c8b890,#5a6a40 50%,#3f6a22)"></div>
  <div class="post-date"><b>02</b><i>Jan</i></div>
  <div class="post-card"><h3>Sed ut perspiciatis unde omnis iste natus error sit...</h3><p>Sed ut perspiciatis unde omnis iste natus error sit voluptatem accusantium......</p></div>
  <div class="read-more">Read More</div>
</article>
<article class="post abs" style="left:446px">
  <div class="post-photo" role="img" aria-label="Aerial photo of green paddocks and stable buildings" style="background:linear-gradient(180deg,#3f6a2a,#6a9a40 50%,#4f7a30)"></div>
  <div class="post-date"><b>02</b><i>Jan</i></div>
  <div class="post-card"><h3>Sed ut perspiciatis unde omnis iste natus error sit...</h3><p>Sed ut perspiciatis unde omnis iste natus error sit voluptatem accusantium......</p></div>
  <div class="read-more is-featured">Read More</div>
</article>
<article class="post abs" style="left:781px">
  <div class="post-photo" role="img" aria-label="Photo of a driveway between tall hedges" style="background:linear-gradient(180deg,#a8c8e8,#2f4a22 40%,#8a7050)"></div>
  <div class="post-date"><b>02</b><i>Jan</i></div>
  <div class="post-card"><h3>Sed ut perspiciatis unde omnis iste natus error sit...</h3><p>Sed ut perspiciatis unde omnis iste natus error sit voluptatem accusantium......</p></div>
  <div class="read-more">Read More</div>
</article>

<footer class="site-footer abs">
  <div class="footer-brand"><span class="brand-dot"></span><span class="brand-name">Marlow Vale Stud</span></div>
  <nav class="footer-nav"><span>Home</span>|<span>About Us</span>|<span>Services</span>|<span>News</span>|<span>Contact Us</span></nav>
  <div class="footer-contact">
    <div><svg width="12" height="12" viewBox="0 0 24 24"><path fill="#fff" d="M6.6 10.8a15.1 15.1 0 0 0 6.6 6.6l2.2-2.2c.3-.3.7-.4 1-.2 1.1.4 2.3.6 3.6.6.6 0 1 .4 1 1V20c0 .6-.4 1-1 1A17 17 0 0 1 3 4c0-.6.4-1 1-1h3.5c.6 0 1 .4 1 1 0 1.3.2 2.5.6 3.6.1.3 0 .7-.2 1z"/></svg>Phone: (000)-121-1231</div>
    <div>|</div>
    <div><svg width="13" height="10" viewBox="0 0 26 20"><rect width="26" height="20" rx="2" fill="#fff"/><path d="M1 2l12 9 12-9" fill="none" stroke="#4a4a4a" stroke-width="2"/></svg>Email: info@marlowvalestud.com</div>
    <div>|</div>
    <div><svg width="10" height="14" viewBox="0 0 20 28"><path fill="#fff" d="M10 0a10 10 0 0 0-10 10c0 7.5 10 18 10 18s10-10.5 10-18A10 10 0 0 0 10 0zm0 14a4 4 0 1 1 0-8 4 4 0 0 1 0 8z"/></svg>43718 Lorem Ipsum Dummy Text Lorem</div>
  </div>
  <p class="copyright">© Copyright -2019 Marlow Vale Stud. All rights reserved.</p>
</footer>

</body>
</html>
```